Stylish Business Cards Wanted

- DOUBLE SIDED Design Required -

High end, edgy cards for a corporate and personal stylist. Must include logo,
Name: Belinda Harwick
Title: Director and Stylist
telephone : +61 8 7142 5809
email: belinda@theloombriefing.example
website: theloombriefing.example
Tag: Corporate Workwear & Uniform Specialist | Personal Stylist
Would like nice icons for telephone, email, website

Target Market(s)

Businesses wanting stylish uniforms, people wanting stylish wardrobes

Industry/Entity Type

Corporate Workwear Stylist

Contact Information for Business Card

I would like black, white and gold foiling incorporated in the design - possibly a touch of the other colours on my branding guide attached Name: Belinda Harwick Title: Director and Stylist telephone : +61 8 7142 5809 email: belinda@theloombriefing.example website: theloombriefing.example Tag: Corporate Workwear & Uniform Specialist | Personal Stylist Would like nice icons for telephone, email, website

Font styles to use
Other font styles liked:
• Raleway

Colors

Designer to choose colors to be used in the design.

Requirements
Must have
• Gold foil accents

```html
<!DOCTYPE html>
<html lang="en">
<head>
<meta charset="utf-8">
<title>The Loom Briefing – Business Cards</title>
<link href="https://fonts.googleapis.com/css2?family=Questrial&display=swap" rel="stylesheet">
<style>
  :root {
    --backdrop: #ebebeb;
    --card: #ffffff;
    --ink: #1d1b1b;
    --gold: #e2b74e;
    --mist: #f2f2f3;
    --rule: #3a3a3a;
  }
  * { margin: 0; padding: 0; box-sizing: border-box; }
  html, body { width: 1200px; height: 507px; overflow: hidden; }
  body {
    background: var(--backdrop);
    font-family: "Questrial", "Century Gothic", sans-serif;
    color: var(--ink);
    position: relative;
  }
  .card {
    position: absolute;
    top: 106px;
    width: 493px;
    height: 295px;
    background: var(--card);
    overflow: hidden;
    box-shadow: 0 8px 18px rgba(0,0,0,0.12);
  }
  .card--front { left: 83px; border: 1px solid #d8d8d8; }
  .card--back { left: 623px; }
  .script-backdrop {
    position: absolute;
    inset: 0;
    background: radial-gradient(ellipse at 55% 55%, var(--mist) 0%, #f9f9f9 55%, var(--card) 85%);
  }
  /* front */
  .brand {
    position: absolute;
    left: 0; right: 0;
    top: 96px;
    display: flex;
    align-items: center;
    justify-content: center;
    gap: 10px;
  }
  .brand__mark {
    width: 12px; height: 12px;
    background: var(--gold);
  }
  .brand__name {
    font-size: 34px;
    color: var(--ink);
    letter-spacing: 0.5px;
  }
  .tagline {
    position: absolute;
    left: 55px;
    top: 221px;
    width: 384px;
    height: 25px;
    padding: 0 4px;
    border: 1px solid var(--rule);
    display: flex;
    align-items: center;
    justify-content: center;
    font-size: 11.3px;
    letter-spacing: -0.2px;
    white-space: nowrap;
    overflow: hidden;
  }
  .tagline__sep { margin: 0 5px; }
  /* back */
  .back__bar {
    position: absolute;
    left: 0; top: 131px;
    width: 32px; height: 19px;
    background: var(--ink);
  }
  .identity {
    position: absolute;
    right: 289px;
    top: 124px;
    text-align: right;
    white-space: nowrap;
  }
  .identity__name {
    color: var(--gold);
    font-size: 23px;
    line-height: 1;
  }
  .identity__title {
    font-size: 11.5px;
    margin-top: 4px;
  }
  .back__divider {
    position: absolute;
    left: 212px; top: 118px;
    width: 1px; height: 60px;
    background: var(--rule);
  }
  .contacts {
    position: absolute;
    left: 221px; top: 117px;
    list-style: none;
  }
  .contacts__item {
    display: flex;
    align-items: center;
    gap: 5px;
    height: 21.5px;
    font-size: 14.2px;
    white-space: nowrap;
  }
  .contacts__icon { width: 11px; height: 11px; flex: none; }
</style>
</head>
<body>

  <section class="card card--front">
    <div class="script-backdrop" role="img" aria-label="Large faint script wordmark decoration"></div>
    <div class="brand">
      <span class="brand__mark"></span>
      <span class="brand__name">The Loom Briefing</span>
    </div>
    <div class="tagline">
      <span>CORPORATE WORKWEAR</span><span class="tagline__sep">|</span>
      <span>UNIFORM SPECIALIST</span><span class="tagline__sep">|</span>
      <span>PERSONAL STYLIST</span>
    </div>
  </section>

  <section class="card card--back">
    <div class="script-backdrop" role="img" aria-label="Large faint script wordmark decoration"></div>
    <div class="back__bar"></div>
    <div class="identity">
      <div class="identity__name">Belinda Harwick</div>
      <div class="identity__title">Director and Stylist</div>
    </div>
    <div class="back__divider"></div>
    <ul class="contacts">
      <li class="contacts__item">
        <svg class="contacts__icon" viewBox="0 0 12 12" aria-hidden="true">
          <circle cx="6" cy="6" r="6" fill="var(--gold)"/>
          <path d="M3 5.2 Q6 2.8 9 5.2 L8.2 6 L7.2 5.4 L7.2 4.8 Q6 4.3 4.8 4.8 L4.8 5.4 L3.8 6 Z M3.8 8.6 L4.6 6.2 L7.4 6.2 L8.2 8.6 Z" fill="#fff"/>
        </svg>
        <span>+61 8 7142 5809</span>
      </li>
      <li class="contacts__item">
        <svg class="contacts__icon" viewBox="0 0 12 12" aria-hidden="true">
          <circle cx="6" cy="6" r="6" fill="var(--gold)"/>
          <rect x="3" y="4" width="6" height="4.2" fill="#fff"/>
          <path d="M3 4 L6 6.4 L9 4" fill="none" stroke="var(--gold)" stroke-width="0.8"/>
        </svg>
        <span>belinda@theloombriefing.example</span>
      </li>
      <li class="contacts__item">
        <svg class="contacts__icon" viewBox="0 0 12 12" aria-hidden="true">
          <circle cx="6" cy="6" r="6" fill="var(--gold)"/>
          <g fill="none" stroke="#fff" stroke-width="0.7">
            <circle cx="6" cy="6" r="3.4"/>
            <ellipse cx="6" cy="6" rx="1.5" ry="3.4"/>
            <line x1="2.6" y1="6" x2="9.4" y2="6"/>
          </g>
        </svg>
        <span>theloombriefing.example</span>
      </li>
    </ul>
  </section>

</body>
</html>
```